Website Design Chair in Business Administration, especially information and service systems

We, the Chair in Business Administration, especially information and service systems, teach in the field of Business Informatics and Business Administration at Velmont University.
We want to setup our current website in a fresh new and clean design because the design of the old page is outdated: http://dkp.uni-velmont.example/en/
The design should be created in a way that we can integrate it into Wordpress later. Furthermore, the website should have the existing website tabs (pages). We want to add the missing subcategories in the tabs, which means that when you move the mouse over a tab, subcategories/side menus should appear.
We have the goal that the website is very clear and that the students get a direct overview especially of the lectures offered. Furthermore the website should be suitable for mobile devices.
Start page:
In general we are interested in a Tile-based Design (2 or more columns) on the start page - similar to this page: https://www.hochschule-brandor.example/. Here, the fields (Digital Process Networks (DPN) with photo, Lectures of the semester, theses, study projects, projects, current events (social media wall), jobs and internship (together), new publications) should be integrated in the form of tiles with a cover picture per field and a short description.
Furthermore, we would like to position a search bar, a social media wall especially for Instagram (replaces the field current events) and the cooperation partners perhaps as sliders with logos of the companies in the lower part of the start page (see Cooperation tab on the far right) on the start page. Footer remains the same.
Research:
Display the same content more attractively.
Learning-Platform:
Furthermore only as link.
Teaching:
In addition to the existing sub-items (Lectures of the semester, teaching-archive, learning platform, theses and book lending), the "Overview of DPN courses" and the " Open Bachelor & Master theses" should be graphically displayed.
Team:
The concept of the Teamgraph including project connections should remain. Furthermore we can imagine to list the employees with photos and short description in form of tiles (1 employee on a tile) below the graph (2 or more columns of tiles).
Publications:
Continue to display a list of publications.
Jobs and internships:
The Open Positions should be divided here into Research Associates, Student Assistants and interns, so that it becomes clearer (3 columns).
Projects:
Here we are interested a Tile-based Design (2 or more columns). We want to integrate the project fields (KORUVAN, Tidal Record Vault etc.) in the form of tiles with a title image per field and a short description.
Events and cooperations should be removed as they are sufficiently represented on the start page.
Target Market(s)
Students as well as current and future project partners
Logo Text
DPN (+ optional Chair in Digital Process Networks)
Coding
Coded - Design and coding required
Number of Pages Required
5+ page
Requirements
Must have
- See description above
Nice to have
- Perhaps a design can be created in which a direct connection to research content (AI, Deep Learning etc.) and to courses (Data Science, AI in companies etc.) can be seen.

```html
<!DOCTYPE html>
<html lang="en">
<head>
<meta charset="utf-8">
<title>Digital Process Networks</title>
<link href="https://fonts.googleapis.com/css2?family=IBM+Plex+Sans:wght@400;500;600;700&family=Poppins:wght@600;700&display=swap" rel="stylesheet">
<style>
:root{
  --navy:#1d2b52;
  --accent:#e8452c;
  --blush:#f4f0f0;
  --mist:#ebebee;
  --text:#333847;
  --line:#c9ccd6;
  --white:#fff;
}
*{box-sizing:border-box;margin:0;padding:0}
html,body{width:1200px;height:4587px;overflow:hidden}
body{font-family:"IBM Plex Sans",sans-serif;color:var(--text);background:var(--white);position:relative}
.abs{position:absolute}
.btn{position:absolute;background:var(--accent);color:var(--white);font-weight:600;letter-spacing:.5px;text-transform:uppercase;display:flex;align-items:center;justify-content:center}
.title{position:absolute;left:0;width:1200px;text-align:center;font-weight:700;font-size:23px;color:var(--navy);letter-spacing:.3px}
.rule{position:absolute;left:575px;width:50px;height:3px;background:var(--navy)}
.photo{position:absolute}
.site-header{position:absolute;top:0;left:0;width:1200px;height:122px;border-bottom:2px solid #e2e2e6}
.brand{left:133px;top:24px;font-weight:700;font-size:24px;color:var(--navy)}
.follow{left:910px;top:31px;font-size:10px;color:#555}
.soc{position:absolute;top:24px;width:27px;height:27px;border-radius:50%;background:var(--navy)}
.topline{position:absolute;left:0;top:72px;width:1200px;height:1px;background:#e2e2e6}
.nav{position:absolute;top:88px;left:133px;display:flex;font-size:13px;font-weight:600;color:#1a1a1a}
.nav span{margin-right:38px}
.hero{top:122px;left:0;width:1200px;height:523px;background:linear-gradient(180deg,#6b6a6e 0%,#8c8178 45%,#4a4543 100%)}
.hero h1{position:absolute;top:62px;width:1200px;text-align:center;font-family:"Poppins",sans-serif;font-size:33px;color:var(--white);text-shadow:0 2px 6px rgba(0,0,0,.4)}
.dots{position:absolute;top:480px;left:562px;display:flex;gap:8px}
.dots i{width:7px;height:7px;border-radius:50%;background:#fff;opacity:.8}
.dots i.on{width:11px;height:11px;margin-top:-2px;background:var(--accent);border:2px solid #fff;opacity:1}
.about{top:645px;left:0;width:1200px;height:477px;background:var(--blush)}
.about h2{position:absolute;left:635px;top:45px;font-size:22px;line-height:31px;color:var(--navy);font-weight:700}
.about p{position:absolute;left:635px;top:148px;width:430px;font-size:12.6px;line-height:20px}
.lectures{top:1122px;left:0;width:1200px;height:418px}
.lect{position:absolute;top:134px;width:226px;height:224px;border:1.5px solid #a9aebd;background:#fff;text-align:center}
.lect svg{position:absolute;left:78px;top:30px}
.lect span{position:absolute;left:0;right:0;top:128px;font-size:12px;line-height:17px;font-weight:500;color:var(--navy)}
.theses{top:1540px;left:0;width:1200px;height:486px;background:var(--blush)}
.theses h2{position:absolute;left:132px;top:35px;font-size:23px;color:var(--navy);font-weight:700;text-decoration:underline;text-underline-offset:5px}
.theses p{position:absolute;left:132px;top:92px;width:400px;font-size:12.6px;line-height:19.5px}
.theses ul{position:absolute;left:132px;top:213px;list-style:none;font-size:12.6px;line-height:24px}
.theses li{padding-left:22px;position:relative}
.theses li::before{content:"";position:absolute;left:2px;top:7px;width:8px;height:4px;border-left:2.5px solid var(--accent);border-bottom:2.5px solid var(--accent);transform:rotate(-45deg)}
.projects{top:2026px;left:0;width:1200px;height:650px}
.tile{position:absolute;width:302px;height:225px}
.tile b{position:absolute;left:18px;bottom:16px;color:#fff;font-size:15.5px;letter-spacing:.3px}
.tile b::before{content:"";position:absolute;left:0;top:-9px;width:24px;height:2px;background:#fff}
.tile em{position:absolute;right:6px;bottom:6px;width:26px;height:26px;background:var(--accent)}
.events{top:2676px;left:0;width:1200px;height:390px;background:var(--blush)}
.ev{position:absolute;top:121px;width:229px;height:230px}
.ev b{position:absolute;left:14px;bottom:14px;color:#fff;font-size:12px;line-height:14px;font-weight:700}
.ev b::before{content:"";position:absolute;left:0;top:-7px;width:22px;height:2px;background:#fff}
.arr{position:absolute;top:222px;width:24px;height:26px;background:#fff;display:flex;align-items:center;justify-content:center}
.pubs{top:3066px;left:0;width:1200px;height:390px;background:var(--mist)}
.pub{position:absolute;top:121px;width:301px;height:228px;background:#fff;padding:34px 35px 0}
.pub h4{font-size:12.5px;color:var(--navy);font-weight:600;margin-bottom:14px;white-space:nowrap}
.pub p{font-size:11.5px;line-height:17.5px}
.pub span{position:absolute;left:37px;top:178px;border:1px solid #bbb;font-size:9.5px;padding:3px 9px}
.partners{top:3456px;left:0;width:1200px;height:300px}
.logo{position:absolute;top:139px;width:180px;height:102px;border:2px solid #b8bcc8;display:flex;align-items:center;justify-content:center;font-size:19px;font-weight:600;color:#1a1a1a}
.chev{position:absolute;top:180px;font-size:30px;color:#999}
.jobs{top:3756px;left:0;width:1200px;height:482px;background:linear-gradient(160deg,#3b4260 0%,#22273a 55%,#3d3a3e 100%)}
.jobs h2{position:absolute;top:54px;width:1200px;text-align:center;font-family:"Poppins",sans-serif;font-size:31px;color:#fff}
.jobs p{position:absolute;top:118px;width:1200px;text-align:center;font-family:"Poppins",sans-serif;font-size:17px;line-height:25px;color:#fff;font-weight:600}
.site-footer{top:4238px;left:0;width:1200px;height:349px;background:var(--navy);color:#fff}
.site-footer .fbrand{position:absolute;left:152px;top:80px;font-family:"Poppins",sans-serif;font-size:28px;line-height:44px;font-weight:600}
.vdiv{position:absolute;left:465px;top:55px;width:1px;height:168px;background:rgba(255,255,255,.25)}
.fh{position:absolute;top:57px;font-size:12px;font-weight:700;letter-spacing:.5px}
.fcol{position:absolute;top:95px;font-size:11px;line-height:20px;letter-spacing:.3px}
.fsoc{position:absolute;left:960px;display:flex;align-items:center;gap:12px;font-size:11px;line-height:15px}
.fsoc i{width:24px;height:24px;border-radius:50%;background:#fff;display:block}
.copy{position:absolute;top:312px;width:1200px;text-align:center;font-size:9.5px;opacity:.85}
</style>
</head>
<body>

<header class="site-header">
  <div class="abs brand">Digital Process Networks</div>
  <div class="abs follow">FOLLOW</div>
  <i class="soc" style="left:967px" aria-label="Friendhub"></i>
  <i class="soc" style="left:1003px" aria-label="Chirper"></i>
  <i class="soc" style="left:1039px" aria-label="Workline"></i>
  <div class="topline"></div>
  <nav class="nav"><span>RESEARCH</span><span>LEARNING-PLATFORM</span><span>TEACHING</span><span>TEAM</span><span>PUBLICATIONS</span><span>JOBS</span><span>PROJECTS</span><span>EVENTS</span><span>COOPERATIONS</span></nav>
</header>

<section class="abs hero" role="img" aria-label="Lecture hall with students listening to a speaker">
  <h1>Digital Process Networks</h1>
  <div class="btn" style="left:526px;top:128px;width:144px;height:40px;font-size:15px">Read more</div>
  <div class="dots"><i></i><i></i><i class="on"></i><i></i><i></i></div>
</section>

<section class="abs about">
  <div class="photo" style="left:137px;top:57px;width:353px;height:236px;background:linear-gradient(135deg,#8d8a7e,#c9c2b2 50%,#5c5a55)" role="img" aria-label="Workshop presentation in a seminar room"></div>
  <div class="photo" style="left:233px;top:190px;width:352px;height:235px;background:linear-gradient(135deg,#7f8a92,#b5bcc0 45%,#4f555c);border:3px solid var(--blush)" role="img" aria-label="Meeting around a conference table"></div>
  <h2>DIGITAL PROCESS<br>NETWORKS (DPN)</h2>
  <p>Chair in Business Administration, especially Digital Process Networks at Velmont University deals with the development and management of data-driven services, for instance healthcare. Directed by Prof. Dr.-Ing. Henrik Lansberg, the chair investigates how the application of experimental design methods combined with distributed, data analytic approaches lead to adaptive service designs and innovative solutions. This research is conducted in basic and applied research projects in cooperation with leading research and industry partners. Results are applied and validated in industry projects by the research group Smart Service Engineering (SSE) at the Northgate Institute for Applied Intelligence (NIAI).</p>
  <div class="btn" style="left:638px;top:398px;width:106px;height:31px;font-size:11.5px">Read more</div>
</section>

<section class="abs lectures">
  <div class="title" style="top:50px">LECTURES OF THE SEMESTER</div>
  <div class="rule" style="top:92px"></div>
  <div class="lect" style="left:132px">
    <svg width="70" height="70" viewBox="0 0 70 70"><circle cx="35" cy="35" r="26" fill="none" stroke="#1d2b52" stroke-width="9" stroke-dasharray="7 5"/><circle cx="35" cy="35" r="21" fill="#1d2b52"/><circle cx="35" cy="30" r="5" fill="#fff"/><circle cx="25" cy="33" r="3.5" fill="#fff"/><circle cx="45" cy="33" r="3.5" fill="#fff"/><path d="M27 45a8 8 0 0 1 16 0z" fill="#fff"/></svg>
    <span>SERVICE<br>MANAGEMENT</span></div>
  <div class="lect" style="left:371px">
    <svg width="70" height="70" viewBox="0 0 70 70"><rect x="12" y="16" width="40" height="40" rx="4" fill="none" stroke="#1d2b52" stroke-width="6"/><path d="M28 44l4-12 22-22 8 8-22 22z" fill="#1d2b52" stroke="#fff" stroke-width="2"/></svg>
    <span>AI IN<br>COMPANIES</span></div>
  <div class="lect" style="left:608px">
    <svg width="70" height="70" viewBox="0 0 70 70"><path d="M20 60V46c-6-4-10-10-10-18 0-13 11-22 24-22s22 9 22 20l6 12h-6v10H44v12z" fill="#1d2b52"/><circle cx="30" cy="24" r="9" fill="#fff"/><circle cx="30" cy="24" r="4" fill="#1d2b52"/></svg>
    <span>SERVICE<br>ENGINEERING</span></div>
  <div class="lect" style="left:845px">
    <svg width="70" height="70" viewBox="0 0 70 70"><rect x="30" y="12" width="34" height="26" fill="none" stroke="#1d2b52" stroke-width="4"/><circle cx="16" cy="18" r="6" fill="#1d2b52"/><path d="M10 28h14l10 6-2 3-8-3v28h-5V48h-3v14h-5V28z" fill="#1d2b52"/><path d="M44 38l-6 20M50 38l6 20" stroke="#1d2b52" stroke-width="3"/></svg>
    <span>SEMINAR "PANDEMIC<br>MONITORING SYSTEMS<br>AND MOBILE APPS"</span></div>
</section>

<section class="abs theses">
  <h2>THESES</h2>
  <p>There are three subject areas available for the editing of theses (Bachelor/Master), projects and internships: (1) Service Design and Management, (2) Data-driven Services, and (3) Conceptual Modeling. Please, submit your application for theses (Bachelor/Master), projects and internships here.</p>
  <ul>
    <li>Smart Services</li>
    <li>Business models in healthcare, e.g., Fitora Health-Kit</li>
    <li>Information systems for health records</li>
    <li>Telematik</li>
    <li>Apps in healthcare</li>
    <li>Adoption of Smart Home Services</li>
    <li>Processing user motives in HCI settings</li>
  </ul>
  <div class="btn" style="left:132px;top:411px;width:107px;height:32px;font-size:11.5px">Read more</div>
  <div class="photo" style="left:578px;top:0;width:622px;height:486px;background:linear-gradient(160deg,#4a3d33 0%,#8a7158 40%,#2e3340 100%)" role="img" aria-label="Speaker addressing an audience in a wood-panelled hall"></div>
</section>

<section class="abs projects">
  <div class="title" style="top:50px">OUR PROJECTS</div>
  <div class="rule" style="top:91px"></div>
  <div class="tile" style="left:114px;top:128px;background:linear-gradient(140deg,#7e8387,#c2c2bd 50%,#4e4f52)" role="img" aria-label="Project team meeting"><b>KORUVAN</b><em></em></div>
  <div class="tile" style="left:431px;top:128px;background:linear-gradient(140deg,#a9bcc5,#dfe6e8 50%,#7b8e98)" role="img" aria-label="Person facing a data network visual"><b>TIDAL RECORD VAULT</b><em></em></div>
  <div class="tile" style="left:748px;top:128px;background:linear-gradient(140deg,#9a8d7d,#d6cfc5 50%,#6d6256)" role="img" aria-label="Busy shopping mall interior"><b>VELTRAMOS</b><em></em></div>
  <div class="tile" style="left:114px;top:367px;background:linear-gradient(180deg,#b8c6cf 0%,#6a6a55 50%,#4b5a2c 100%)" role="img" aria-label="Tractor working a field"><b>FIELD SENSE WORLD</b><em></em></div>
  <div class="tile" style="left:431px;top:367px;background:linear-gradient(180deg,#28476d 0%,#7a5a3c 55%,#3c4650 100%)" role="img" aria-label="Container ship at port"><b>QUARVIS</b><em></em></div>
  <div class="tile" style="left:748px;top:367px;background:linear-gradient(140deg,#b9c5cc,#5d7f95 50%,#34404a)" role="img" aria-label="Laptop with a security graphic"><b>LYNDORA</b><em></em></div>
</section>

<section class="abs events">
  <div class="title" style="top:40px">CURRENT EVENTS</div>
  <div class="rule" style="top:81px"></div>
  <div class="ev" style="left:10px;background:linear-gradient(140deg,#7e8387,#c4c4bf 50%,#4e4f52)" role="img" aria-label="Consortial meeting"><b>KORUVAN CONSORTIAL<br>MEETING</b></div>
  <div class="ev" style="left:246px;background:linear-gradient(140deg,#6c6a60,#b2ab98 50%,#3f3d38)" role="img" aria-label="Workshop group"><b>KORUVAN AP 2<br>WORKSHOP</b></div>
  <div class="ev" style="left:483px;background:linear-gradient(140deg,#9aa2a5,#d5d7d5 50%,#3d4247)" role="img" aria-label="Project group photo"><b>PROJEKT TIDAL<br>RECORD VAULT</b></div>
  <div class="ev" style="left:723px;background:linear-gradient(180deg,#6d8aa8,#c5cfd6 50%,#3a3e48)" role="img" aria-label="Consortium group photo"><b>KORUVAN CONSORTIAL<br>MEETING</b></div>
  <div class="ev" style="left:962px;background:linear-gradient(140deg,#b6b8bf,#e3e3e6 45%,#3b3f4c)" role="img" aria-label="Workshop group photo"><b>KORUVAN AP 2<br>WORKSHOP</b></div>
  <div class="arr" style="left:8px"><svg width="8" height="12"><path d="M7 1L2 6l5 5" fill="none" stroke="#333" stroke-width="2"/></svg></div>
  <div class="arr" style="left:1170px"><svg width="8" height="12"><path d="M1 1l5 5-5 5" fill="none" stroke="#333" stroke-width="2"/></svg></div>
</section>

<section class="abs pubs">
  <div class="title" style="top:52px">PUBLICATIONS</div>
  <div class="rule" style="top:93px"></div>
  <article class="pub" style="left:134px"><h4>Halvorsen, T., &amp; Lansberg, H.</h4><p>A Situation-Specific Smart Retail Service Based On Vital Signs, Proceedings of the 41th International Conference on Information Systems, 2020.</p><span>PDF (3.62 MB)</span></article>
  <article class="pub" style="left:452px"><h4>Halvorsen, T., &amp; Lansberg, H.</h4><p>Data-Driven System for Treatment of Obese Children in Rural Areas, MobileHX '20 Workshop: Learning from mHealth Success Stories: Effective Interventions for Marginalised Populations, 2020.</p><span>PDF (3.62 MB)</span></article>
  <article class="pub" style="left:769px"><h4>Ng, A.; Dahl, J.; Orr, P. &amp; Lansberg, H.</h4><p>CD2 : Combined Distances of Contrast Distributions for the Assessment of Perceptual Quality of Image Processing, POSTER presentation at VISCON'20, 2019.</p><span>PDF (3.62 MB)</span></article>
</section>

<section class="abs partners">
  <div class="title" style="top:52px">OUR PARTNERS</div>
  <div class="rule" style="top:93px"></div>
  <div class="chev" style="left:76px">‹</div>
  <div class="logo" style="left:129px">VANTRA</div>
  <div class="logo" style="left:322px">Clientwise</div>
  <div class="logo" style="left:515px">Paylinq</div>
  <div class="logo" style="left:706px">Hartwell Group</div>
  <div class="logo" style="left:895px">Seabrook</div>
  <div class="chev" style="left:1104px">›</div>
</section>

<section class="abs jobs" role="img" aria-label="Speaker at a lectern presenting to a seated audience">
  <h2>JOBS AND INTERNSHIP</h2>
  <p>GAIN PRACTICAL EXPERIENCE IN AN INTERNSHIP<br>WITH US –BECOME A MEMBER OF THE TEAM!</p>
  <div class="btn" style="left:529px;top:180px;width:142px;height:39px;font-size:15px">Read more</div>
</section>

<footer class="abs site-footer">
  <div class="fbrand">Digital Process<br>Networks</div>
  <div class="vdiv"></div>
  <div class="fh" style="left:571px">MENU</div>
  <div class="fcol" style="left:571px">RESEARCH<br>LEARNING-PLATFORM<br>TEACHING<br>TEAM<br>PUBLICATIONS</div>
  <div class="fcol" style="left:746px">JOBS<br>PROJECTS<br>EVENTS<br>COOPERATIONS</div>
  <div class="fh" style="left:960px">FOLLOW US</div>
  <div class="fsoc" style="top:92px"><i></i><span>Like us on<br>FRIENDHUB</span></div>
  <div class="fsoc" style="top:142px"><i></i><span>Follow us on<br>CHIRPER</span></div>
  <div class="fsoc" style="top:193px"><i></i><span>Follow us on<br>WORKLINE</span></div>
  <div class="copy">Copyright © 2020 All Rights Reserved</div>
</footer>

</body>
</html>
```